Website for a Psychologist in Private Practice

I need a cool web design for my website: www.drkalvoric.com. I would like it to look professional. Keep all the current content and add: Space for video; radio spots (see Silver Cedar Tunes Logo below for those); Quick Inquiry; Friendora link; 5 star rating on Rivo; a map; reviews from former patients. I am open to suggestions.

Target Market(s)

Those seeking individual and marital counseling.

Industry/Entity Type

Mental Health

Number of Pages Required

1 page

Font styles to use
Sans Serif
Other font styles liked:
• I'm open but no hard to read script

Requirements
Must have
• All the content on my home page with link for video and radio spots. List services and degrees and expertices (pics not necessary).
Nice to have
• A video of me and radio conversations (logo of Silver Cedar Tunes radio attached).
Should not have
• Cartoons, comedy, etc.... I don't need pictures of services (marital, depression, etc...) Just list those.

```html
<!DOCTYPE html>
<html lang="en">
<head>
<meta charset="utf-8">
<title>Dr. Marla J. Kalvoric – Psychologist</title>
<link href="https://fonts.googleapis.com/css2?family=Ropa+Sans&family=Arimo:ital,wght@0,400;0,700;1,400;1,700&family=Tinos&display=swap" rel="stylesheet">
<style>
:root{
  --blue:#2f86c6;
  --blue-dark:#1d6fae;
  --ink:#222;
  --muted:#555;
  --rule:#d4d4d4;
  --panel:#f2f2f2;
  --footer:#231f20;
  --white:#fff;
}
*{box-sizing:border-box;margin:0;padding:0}
html,body{width:744px;height:1200px;overflow:hidden;background:var(--white)}
body{position:relative;font-family:"Arimo",Arial,sans-serif;color:var(--ink)}
.abs{position:absolute}
.head-font{font-family:"Ropa Sans",Arial,sans-serif}

/* hero backdrop */
.backdrop{left:0;top:0;width:744px;height:376px;background:linear-gradient(180deg,#3d76a8 0%,#6fa7c9 35%,#5bb0bd 55%,#c9b89a 80%,#d8c6a8 100%)}
.topbar{left:82px;top:0;width:580px;height:58px;background:rgba(20,45,70,.45)}
.site-name{left:90px;top:18px;font-size:24px;color:var(--white)}
.license{left:440px;top:34px;font-size:10px;color:var(--white)}
.call-label{left:577px;top:18px;font-size:9.5px;color:var(--white)}
.call-number{left:579px;top:31px;font-size:14px;color:var(--white)}
.phone-icon{left:553px;top:22px}

.nav{left:82px;top:58px;width:580px;height:28px;background:var(--blue);display:flex;align-items:center}
.nav a{font-family:"Ropa Sans",Arial,sans-serif;color:var(--white);text-decoration:none;font-size:11px;height:28px;line-height:28px;padding:0 10px;border-right:1px solid rgba(255,255,255,.25)}
.nav a.active{background:var(--white);color:#1a3550}
.nav a:last-of-type{border-right:none}
.follow{left:558px;top:67px;font-size:8.5px;color:var(--white);font-family:"Ropa Sans",Arial,sans-serif}
.social{top:63px;width:17px;height:17px;border-radius:50%}

.slide{left:82px;top:86px;width:580px;height:272px;background:linear-gradient(180deg,#8fb3cc 0%,#e9d9a8 40%,#f4e9b8 55%,#9fb54b 75%,#7c9b2e 100%)}
.slide-kicker{left:146px;top:167px;font-size:18px;color:var(--blue)}
.slide-text{left:146px;top:194px;width:190px;font-size:14.5px;line-height:21px;color:#2a2a2a}
.arrow{top:211px;width:21px;height:20px;background:#333;display:flex;align-items:center;justify-content:center}

/* section headings */
.h2{font-family:"Ropa Sans",Arial,sans-serif;font-size:14.5px;color:var(--ink)}
.rule{height:3px;background:var(--rule)}
.rule::after{content:"";display:block;width:35px;height:3px;background:var(--blue)}

.bio{left:83px;top:426px;width:172px;font-family:"Tinos",serif;font-size:9.4px;line-height:13.1px;color:#333;text-align:justify}
.link{font-size:9px;color:#333;text-decoration:underline}
.vline{width:1px;background:#e2e2e2}

.avatar{border-radius:50%;background:radial-gradient(circle at 50% 40%,#e6c9a0,#8a6a48 70%,#3f4c66)}
.expert-name{left:358px;top:434px;font-family:"Ropa Sans",Arial,sans-serif;font-size:14px;line-height:18px;color:var(--ink)}
.expert-list{left:292px;top:487px;list-style:none;font-family:"Tinos",serif;font-size:9px;line-height:13px;color:#333}
.expert-list li{display:flex;align-items:center;gap:4px}

.quote-box{left:481px;top:428px;width:176px;height:105px;border:1px solid #d8d8d8;border-radius:3px;padding:6px 8px 6px 9px;font-size:8.6px;line-height:13px;color:#333}
.quote-author{display:block;text-align:right;margin-top:6px;font-family:"Tinos",serif;font-size:8px}

.degrees{left:81px;top:579px;width:581px;height:48px;background:var(--blue);color:var(--white)}
.deg-title{left:67px;top:14px;font-family:"Ropa Sans",Arial,sans-serif;font-size:14.5px}
.deg-item{font-family:"Ropa Sans",Arial,sans-serif;font-size:9px}

.video{left:88px;top:677px;width:182px;height:138px;border:2px solid var(--blue);background:radial-gradient(circle at 50% 50%,#c9a77f,#5d6f8a 75%)}
.play{left:161px;top:737px}

.lead{left:295px;top:681px;font-size:7.6px;color:#333}
.field{left:294px;width:171px;height:19px;border:1px solid #d6d6d6;font-size:7.5px;color:#666;padding:5px 0 0 6px;background:var(--white)}
.submit{left:294px;top:797px;width:68px;height:19px;background:var(--blue);color:var(--white);font-size:9.5px;font-weight:700;text-align:center;line-height:19px}

.radio-ad{left:486px;top:652px;width:163px;height:163px;background:linear-gradient(160deg,#d8234a 0%,#b01a3c 45%,#5b4a46 100%)}
.radio-ad-name{left:6px;top:3px;font-family:"Ropa Sans",Arial,sans-serif;font-size:13px;color:var(--white)}
.radio-ad-times{left:5px;top:123px;font-family:"Ropa Sans",Arial,sans-serif;color:var(--white);font-size:8px;line-height:9px}

.reviews{left:0;top:842px;width:744px;height:180px;background:var(--panel)}
.reviews-title{left:0;top:17px;width:744px;text-align:center;font-family:"Ropa Sans",Arial,sans-serif;font-size:15px}
.reviews-rule{left:278px;top:38px;width:188px;height:2px;background:#c8c8c8}
.reviews-rule-accent{left:350px;top:38px;width:44px;height:2px;background:var(--blue)}
.review-text{left:172px;top:59px;width:480px;font-size:8.4px;line-height:14.6px;font-style:italic;color:#222}
.review-by{left:174px;top:128px;font-size:8.2px;font-style:italic;font-weight:700}
.more{left:563px;top:141px;font-size:8.2px;color:#444}

.footer{left:0;top:1022px;width:744px;height:152px;background:var(--footer);color:#e8e8e8}
.f-title{font-family:"Ropa Sans",Arial,sans-serif;font-size:10px;padding-bottom:4px;border-bottom:1px dashed #666}
.f-links{list-style:none;font-size:8.2px;line-height:13.8px}
.f-links li:first-child{color:#d7a35a}
.contact{font-size:8.2px;line-height:11.5px}
.badge-a{left:212px;top:1061px;width:128px;height:49px;background:#fff;border:2px solid var(--blue)}
.badge-b{left:212px;top:1115px;width:128px;height:48px;background:#8fa83b;border:2px solid var(--blue)}
.rating{left:595px;top:1058px;width:51px;height:50px;border-radius:6px;background:#c8232c;border:2px solid #e6e6e6}
.share{left:592px;top:1120px;width:58px;height:19px;background:#3b5a9a;border:1px solid #7f95c4;color:var(--white);font-size:8px;display:flex;align-items:center;gap:5px;padding-left:4px}
.share span.sq{width:10px;height:10px;background:var(--white)}
.copyright{left:0;top:1174px;width:744px;height:26px;background:var(--blue);color:var(--white);font-size:8px;text-align:center;line-height:26px}
</style>
</head>
<body>

<header>
  <div class="abs backdrop" role="img" aria-label="Beach and turquoise sea background"></div>
  <div class="abs topbar"></div>
  <div class="abs site-name head-font">Dr. Marla J. Kalvoric</div>
  <div class="abs license head-font">California # PSY20581</div>
  <svg class="abs phone-icon" width="18" height="18" viewBox="0 0 18 18" aria-hidden="true">
    <circle cx="9" cy="9" r="8" fill="none" stroke="#fff" stroke-width="1.2"/>
    <path d="M6.5 5.5c.5-.6 1.2-.6 1.5 0l.6 1.2c.2.4 0 .8-.3 1.1-.3.3-.2.7.1 1.2.4.6.9 1.1 1.4 1.3.4.2.7.1 1-.2.3-.3.7-.4 1.1-.2l1 .7c.5.3.4 1-.2 1.4-1 .8-2.8.3-4.4-1.3S5.6 6.6 6.5 5.5z" fill="#fff"/>
  </svg>
  <div class="abs call-label">Call Us Today</div>
  <div class="abs call-number">949-555-0183</div>

  <nav class="abs nav">
    <a class="active" href="#">Home</a>
    <a href="#">About Me</a>
    <a href="#">Sessions</a>
    <a href="#">Resources</a>
    <a href="#">BIO</a>
    <a href="#">Customer Reviews</a>
    <a href="#">Contact Us</a>
  </nav>
  <div class="abs follow">Follow Us On</div>
  <span class="abs social" style="left:614px;background:#3b5a9a" role="img" aria-label="Friendora"></span>
  <span class="abs social" style="left:640px;background:#2aa9e0" role="img" aria-label="Chirpline"></span>

  <section class="abs slide" role="img" aria-label="Man with open arms in a sunlit meadow"></section>
  <div class="abs slide-kicker head-font">DO NOT COMPROMISE</div>
  <p class="abs slide-text head-font">Experience separates good psychologists from others with fewer and more proficient sessions</p>
  <div class="abs arrow" style="left:86px"><svg width="8" height="10" viewBox="0 0 8 10"><path d="M6 1L2 5l4 4" stroke="#fff" stroke-width="2" fill="none"/></svg></div>
  <div class="abs arrow" style="left:634px"><svg width="8" height="10" viewBox="0 0 8 10"><path d="M2 1l4 4-4 4" stroke="#fff" stroke-width="2" fill="none"/></svg></div>
</header>

<main>
  <!-- Biography -->
  <h2 class="abs h2" style="left:83px;top:393px">My Biography</h2>
  <div class="abs rule" style="left:83px;top:413px;width:172px"></div>
  <p class="abs bio">While I acknowledge the importance of my education, I also appreciate the role my experiences have played in allowing me to relate so well to others. Allow me to share those I feel are most relevant with you. I survived an abusive childhood that my mother &amp; sister unfortunately did not. &amp; it was my grief &amp; desire to become stronger than my past that led me to counseling.....</p>
  <a class="abs link head-font" style="left:83px;top:546px;font-size:9.5px">Read More</a>
  <div class="abs vline" style="left:272px;top:420px;height:132px"></div>

  <!-- Expertise -->
  <h2 class="abs h2" style="left:289px;top:392px">My Expertise</h2>
  <div class="abs rule" style="left:289px;top:413px;width:172px"></div>
  <div class="abs avatar" style="left:287px;top:424px;width:62px;height:62px" role="img" aria-label="Portrait of Dr. Kalvoric"></div>
  <div class="abs expert-name">Dr. Marla J.<br>Kalvoric</div>
  <ul class="abs expert-list">
    <li><svg width="9" height="8" viewBox="0 0 9 8"><path d="M1 4l2.5 3L8 1" stroke="#2f86c6" stroke-width="1.6" fill="none"/></svg>Dating, Marriage,</li>
    <li><svg width="9" height="8" viewBox="0 0 9 8"><path d="M1 4l2.5 3L8 1" stroke="#2f86c6" stroke-width="1.6" fill="none"/></svg>Parenting &amp; Professional Relationships</li>
    <li><svg width="9" height="8" viewBox="0 0 9 8"><path d="M1 4l2.5 3L8 1" stroke="#2f86c6" stroke-width="1.6" fill="none"/></svg>Depression &amp; Anxiety Issues</li>
    <li><svg width="9" height="8" viewBox="0 0 9 8"><path d="M1 4l2.5 3L8 1" stroke="#2f86c6" stroke-width="1.6" fill="none"/></svg>Personality Disorders</li>
    <li><svg width="9" height="8" viewBox="0 0 9 8"><path d="M1 4l2.5 3L8 1" stroke="#2f86c6" stroke-width="1.6" fill="none"/></svg>Life Management</li>
  </ul>
  <div class="abs vline" style="left:471px;top:420px;height:132px"></div>

  <!-- Radio conversations -->
  <h2 class="abs h2" style="left:482px;top:393px">Radio Conversations</h2>
  <div class="abs rule" style="left:482px;top:413px;width:173px"></div>
  <blockquote class="abs quote-box"><span style="color:#999;font-size:13px;font-family:Tinos,serif">&ldquo;</span> Lorem ipsum dolor sit ae onsectetuer adipiscing elit, sed diam nonummy nibh euis tincidunt ut laoreetlore gna aliquam erat olutpat. Ut wisi enim adinim veniam, quis strud xerci tation ullamrper suscipit lobortis sl ut al lorem.<span class="quote-author">Nora Bell</span></blockquote>
  <a class="abs link" style="left:482px;top:541px">View All</a>

  <!-- Degrees -->
  <section class="abs degrees">
    <div class="abs deg-title">My Degrees</div>
    <svg class="abs" style="left:148px;top:7px" width="12" height="34" viewBox="0 0 12 34"><path d="M2 1c5 0 5 3 5 8s1 8 4 8c-3 0-4 3-4 8s0 8-5 8" stroke="rgba(255,255,255,.7)" stroke-width="1.3" fill="none"/></svg>
    <div class="abs deg-item" style="left:171px;top:11px">Doctoral Degree in Clinical Psychology</div>
    <div class="abs deg-item" style="left:171px;top:28px">Masters Degree in Counseling Psychology</div>
    <div class="abs deg-item" style="left:361px;top:11px">Doctoral Internship, Bayline Medical Center</div>
    <div class="abs deg-item" style="left:361px;top:28px">Masters Internship, Harbor Ridge Clinic</div>
  </section>

  <!-- Video -->
  <h2 class="abs h2" style="left:88px;top:649px">View Video</h2>
  <div class="abs rule" style="left:88px;top:668px;width:182px"></div>
  <div class="abs video" role="img" aria-label="Introductory video of Dr. Kalvoric"></div>
  <svg class="abs play" width="18" height="18" viewBox="0 0 18 18" aria-hidden="true"><circle cx="9" cy="9" r="8" fill="none" stroke="#fff" stroke-width="1.5"/><path d="M7 5.5l5 3.5-5 3.5z" fill="#fff"/></svg>

  <!-- Quick inquiry -->
  <h2 class="abs h2" style="left:293px;top:649px">Quick Inquiry</h2>
  <div class="abs rule" style="left:293px;top:668px;width:173px"></div>
  <p class="abs lead">Lorem ipsum dolor sit amet, consectetuer</p>
  <div class="abs field" style="top:696px">Name</div>
  <div class="abs field" style="top:718px">Email</div>
  <div class="abs field" style="top:740px">Phone</div>
  <div class="abs field" style="top:762px;height:30px">Message</div>
  <div class="abs submit">SUBMIT</div>

  <!-- Radio show -->
  <section class="abs radio-ad" role="img" aria-label="Radio show promotion with hosts">
    <div class="abs radio-ad-name">SILVER CEDAR TUNES</div>
    <div class="abs radio-ad-times"><span style="font-size:12px">SUNDAYS</span><br>4PM PST/7PM EST<br>TUNEWAVE.NET</div>
  </section>

  <!-- Reviews -->
  <section class="abs reviews">
    <h2 class="abs reviews-title">Reviews From Former Patients</h2>
    <div class="abs reviews-rule"></div>
    <div class="abs reviews-rule-accent"></div>
    <div class="abs avatar" style="left:89px;top:56px;width:71px;height:71px" role="img" aria-label="Portrait of a former patient"></div>
    <p class="abs review-text">Lorem ipsum dolor sit amet, consectetuer adipiscing elit, sed diam nonummy nibh euismod tincidunt ut laoreet dolore magna aliquam erat volutpat. Ut wisi enim ad minim veniam, quis nostrud exerci tation ullamcorper suscipit lobortis nisl ut aliquip commodo consequat. Duis autem vel eum iriure dolor in hendrerit in vulputate velit esse molestie consequat, vel illum dolore eu feugiat nulla facilisis at vero eros et accumsan et iusto odio dignissimaugue duis dolore te feugait nulla facilisi.</p>
    <div class="abs review-by">.... Lorem Ispum, Manger</div>
    <div class="abs more"><span style="text-decoration:underline">Read more testimonials</span> &raquo;</div>
  </section>
</main>

<footer>
  <div class="abs footer">
    <div class="abs f-title" style="left:90px;top:19px;width:73px">Quick Links</div>
    <ul class="abs f-links" style="left:90px;top:42px">
      <li>Home</li><li>About Me</li><li>Sessions</li><li>Resources</li><li>BIO</li><li>Customer Reviews</li><li>Contact Me</li>
    </ul>
    <div class="abs f-title" style="left:212px;top:19px;width:158px">A Portion of All Revenue Is Donated To</div>
    <div class="abs f-title" style="left:423px;top:19px;width:118px">Contact Details</div>
    <div class="abs contact" style="left:423px;top:42px">A:</div>
    <div class="abs contact" style="left:441px;top:42px">418 Harbor Lane, Suite 210<br>Seaview, CA 92661</div>
    <div class="abs contact" style="left:423px;top:77px">P:</div><div class="abs contact" style="left:441px;top:77px">949-555-0183</div>
    <div class="abs contact" style="left:423px;top:98px">TF:</div><div class="abs contact" style="left:442px;top:98px">949-555-0183</div>
    <div class="abs contact" style="left:423px;top:119px">E:</div><div class="abs contact" style="left:442px;top:119px">mk@drkalvoric.com</div>
  </div>
  <div class="abs badge-a" role="img" aria-label="Child advocacy charity partner"></div>
  <div class="abs badge-b" role="img" aria-label="Family support charity partner"></div>
  <div class="abs rating" role="img" aria-label="Five star rating on Rivo"></div>
  <div class="abs share" aria-label="Share on Friendora"><span class="sq"></span>SHARE</div>
  <div class="abs copyright">Copyright &copy; 2016 Dr. Marla J. Kalvoric &nbsp;All rights reserved</div>
</footer>

</body>
</html>
```